Redesign of outdated "Automotive Automation Company"

We are looking to finally update our outdated website with some cutting edge graphics. We want our customers to know we value technology and are cutting edge as far as design. We provide automation solutions for the automotive industry which essentially means we program robots, and sell automation related products.

Current URL

http://lnk.qorvi.example/Tm4pzr
Updates

Project Deadline Extended
Reason: The client portal wasn't working, it's just finally been fixed by Pixel Harbor. I will go through and start reviewing designs.

We are trying to go with the same look and feel on our business cards, line cards, apparel, etc. so we are forming a brand. I have included the current draft of the line card. Please utilize our newest Logo VEL Standardized Logo.jpg http://img.plomtra.example/zuKe9rb.jpg?1 Also we are trying hard to sell the following software / hardware companies so we can put some emphasis on their product. Corvane Systems https://www.corvanesystems.example/ We make money on selling the software and then on the integration. I think you should tie in this animation. ยท Shop Line Muddle to Momentum https://media.vuntelo.example/clips/9b2e7f1d04c3a85e6f2d1b7c9a0e4f3d8c6b2a1e.jpg?image_play_button=true&image_play_button_color=7b796ae0&image_crop_resized=275x155 In this 2-minute video, discover how Trellan can help run your plant floor. We are Authorized Integrators / Resellers for Pembry Controls Hadrix Sensorik http://hadrix.example/en/usa/ Corvane Systems https://www.corvanesystems.example/ Unified Motion Works www.umwkq.example Brisk Beltway Corp www.briskbeltway.example Castmere Fabrication http://www.castmerefab.example/strategic_partners.aspx

Target Market(s)

Large automotive companies looking for automation or robotic programming. So Professional is key.

Industry/Entity Type

Automotive

Font styles to use
Other font styles liked:
• Possible Open Sans or Lato

Colors
0591cc
ceeaf6
fbd4d5
fbf289
fece3e

Requirements
Must have
• Professional Modern Design.

I want a homepage design, and a rough Sales Page... Where numerous products can be listed.
Nice to have
• Maybe an updated logo if possible.

```html
<!DOCTYPE html>
<html lang="en">
<head>
<meta charset="utf-8">
<title>VEL Engineering Solutions</title>
<link href="https://fonts.googleapis.com/css2?family=Open+Sans:wght@400;600;700&family=Roboto:wght@500&display=swap" rel="stylesheet">
<style>
:root{
  --page:#e8e8e8;
  --ink:#333333;
  --body-ink:#555555;
  --blue:#0591cc;
  --blue-light:#1ab4e0;
  --red:#e0144c;
  --red-light:#f0305e;
  --olive:#b3b414;
  --olive-light:#d3d124;
  --green:#5c9a2a;
  --green-light:#7cbb3c;
  --yellow:#f3e41a;
  --yellow-dark:#c8b600;
  --footer:#2a2a2a;
  --footer-ink:#9a9a9a;
}
*{margin:0;padding:0;box-sizing:border-box}
html,body{width:920px;height:1200px;overflow:hidden}
body{font-family:"Open Sans",Arial,sans-serif;background:var(--page);color:var(--ink);position:relative}

.site-header{position:absolute;left:0;top:0;width:920px;height:113px;background:var(--page)}
.brand{position:absolute;left:46px;top:30px;display:flex;align-items:center;gap:8px}
.brand-mark{width:40px;height:40px;border-radius:50%;background:var(--red)}
.brand-name{font-size:15px;font-weight:700;color:var(--ink);line-height:1.2}
.call-us{position:absolute;left:491px;top:69px;font-size:13.5px;font-weight:600;color:#222}
.payments{position:absolute;left:661px;top:36px;width:213px;height:48px;border:1px solid #c9c9c9;border-radius:3px;background:#f3f3f3;display:flex;align-items:center;justify-content:center;gap:6px;padding-top:10px}
.payments span{display:block;width:47px;height:28px;border-radius:2px}
.pay-a{background:#c9262c}.pay-b{background:#ffffff;border:1px solid #ddd}.pay-c{background:#f4f4f4;border:1px solid #ddd}.pay-d{background:#2a8fd8;width:32px!important}

.main-nav{position:absolute;left:0;top:113px;width:920px;height:38px;background:linear-gradient(#1cb6e2,#0791c5);display:flex;align-items:center;padding-left:45px}
.main-nav a{color:#fff;font-size:11.5px;text-decoration:none}
.main-nav .sep{color:#fff;font-size:11.5px;margin:0 19px}

.hero{position:absolute;left:0;top:151px;width:920px;height:265px;background:linear-gradient(90deg,#2a2a2a 55%,#111 80%,#000)}
.hero-visual{position:absolute;left:0;top:0;width:540px;height:265px;background:radial-gradient(ellipse at 60% 45%,#e6e8ea 0%,#b8bcc0 45%,#3a3a3a 85%)}
.hero-copy{position:absolute;left:592px;top:62px;width:230px}
.hero-copy h2{font-size:21.5px;font-weight:400;color:#fff}
.hero-copy p{font-size:9.2px;color:#ccc;line-height:12.5px;margin-top:9px}
.btn{display:inline-block;color:#fff;text-decoration:none;border-radius:3px;font-size:9.5px;font-weight:600;text-align:center}
.btn-yellow{position:absolute;left:4px;top:83px;width:79px;height:31px;line-height:31px;background:linear-gradient(var(--yellow),var(--yellow-dark));color:#333}
.slider-dots{position:absolute;left:596px;top:188px;display:flex;gap:6px}
.slider-dots i{width:5px;height:5px;border-radius:50%;background:#bbb}
.slider-dots i:first-child{background:var(--blue-light)}

.welcome{position:absolute;left:0;top:416px;width:920px;height:187px;background:#fff;text-align:center}
.welcome h1{font-size:21px;font-weight:600;color:var(--ink);margin-top:32px}
.welcome p{font-size:10px;line-height:17px;color:var(--body-ink);margin:14px auto 0;width:830px}
.btn-blue{margin-top:17px;width:75px;height:27px;line-height:27px;background:linear-gradient(var(--blue-light),var(--blue))}
.band-shadow{position:absolute;left:140px;width:640px;height:10px;border-radius:50%;box-shadow:0 6px 10px rgba(0,0,0,.35)}

.features{position:absolute;left:46px;top:634px;display:flex;gap:10px}
.card{width:200px;height:447px;background:linear-gradient(#fff,#e9e9e9);position:relative}
.card-head{height:48px;color:#fff;font-family:"Roboto",Arial,sans-serif;font-weight:500;font-size:13.5px;padding:15px 13px}
.card-photo{position:absolute;left:10px;top:58px;width:180px;height:121px}
.card-text{position:absolute;left:11px;top:189px;width:180px;font-size:9.2px;line-height:17px;color:#444}
.card-list{position:absolute;left:11px;top:269px;list-style:none;font-size:10px;line-height:17px}
.card-list li{padding-left:13px;position:relative}
.card-list li::before{content:"";position:absolute;left:0;top:5px;border-left:4px solid currentColor;border-top:3.5px solid transparent;border-bottom:3.5px solid transparent}
.card .btn{position:absolute;left:10px;top:413px;height:23px;line-height:23px;padding:0 7px;font-weight:400;font-size:9.5px}
.red .card-head{background:linear-gradient(var(--red-light),var(--red))}.red .card-list{color:var(--red)}.red .btn{background:var(--red)}
.olive .card-head{background:linear-gradient(var(--olive-light),var(--olive))}.olive .card-list{color:var(--olive)}.olive .btn{background:var(--olive)}
.green .card-head{background:linear-gradient(var(--green-light),var(--green))}.green .card-list{color:var(--green)}.green .btn{background:var(--green)}
.green .card-list li{color:#444}.green .card-list li::before{color:var(--green)}
.blue .card-head{background:linear-gradient(var(--blue-light),var(--blue))}.blue .card-list{color:var(--blue)}.blue .btn{background:var(--blue)}

.site-footer{position:absolute;left:0;top:1108px;width:920px;height:92px;background:var(--footer)}
.footer-nav{position:absolute;left:46px;top:25px;font-size:10.5px;color:var(--footer-ink)}
.footer-nav .sep{margin:0 6px}
.copyright{position:absolute;left:46px;top:46px;font-size:10.5px;color:var(--footer-ink)}
.social{position:absolute;left:723px;top:26px;display:flex;gap:6px}
.social span{width:26px;height:26px;background:#3a3a3a}
</style>
</head>
<body>
<header class="site-header">
  <div class="brand"><span class="brand-mark"></span><span class="brand-name">VEL Engineering<br>Solutions</span></div>
  <div class="call-us">Call us: 1-855-MECH-RUN</div>
  <div class="payments" aria-label="Accepted payment methods"><span class="pay-a"></span><span class="pay-b"></span><span class="pay-c"></span><span class="pay-d"></span></div>
</header>

<nav class="main-nav">
  <a href="#">Home</a><span class="sep">|</span><a href="#">About us</a><span class="sep">|</span><a href="#">Services</a><span class="sep">|</span><a href="#">Solutions</a><span class="sep">|</span><a href="#">Technologies</a><span class="sep">|</span><a href="#">Support</a><span class="sep">|</span><a href="#">News</a><span class="sep">|</span><a href="#">Contact us</a>
</nav>

<section class="hero">
  <div class="hero-visual" role="img" aria-label="White humanoid robot head with chrome cables"></div>
  <div class="hero-copy">
    <h2>Program Robots</h2>
    <p>Nemo enim ipsam voluptatem quia voluptas sit aspernatur aut odit aut fugit,</p>
    <a class="btn btn-yellow" href="#">View Details</a>
  </div>
  <div class="slider-dots"><i></i><i></i><i></i></div>
</section>
<div class="band-shadow" style="top:406px"></div>

<section class="welcome">
  <h1>Welcome to velengsolutions</h1>
  <p>Each situation (and company) is unique. A One-size-fits-all&nbsp; approach will never be the optimal solution for your business to reach its full potential. A detailed evaluation of your company's operation and a custom solution provided by VEL Engineering Solutions will take advantage of opportunities specific to your process.<br>That's what we deliver to you.</p>
  <a class="btn btn-blue" href="#">Read More</a>
</section>
<div class="band-shadow" style="top:593px"></div>

<main class="features">
  <article class="card red">
    <h3 class="card-head">SPECIALIZING AREAS</h3>
    <div class="card-photo" role="img" aria-label="Red and white armoured robot" style="background:linear-gradient(#8a8d90,#3c3c3e)"></div>
    <p class="card-text">Provide electrical and mechanical expertise to solve automation specific application problems by utilizing best known industry practices.</p>
    <ul class="card-list"><li>2D and 3D Capabilities</li><li>Applications</li><li>Automation Product Sales</li><li>Consulting</li><li>Onsite Startup and Engineering</li><li>Support</li><li>Contract Engineering /Techs</li><li>Panel Builds</li></ul>
    <a class="btn" href="#">View More</a>
  </article>
  <article class="card olive">
    <h3 class="card-head">EXPERTISE AREAS</h3>
    <div class="card-photo" role="img" aria-label="Metallic skeletal robots" style="background:linear-gradient(#4a4540,#1a1816)"></div>
    <p class="card-text">Provide electrical, mechanical, controls and software expertise to program, startup, debug and commission automated machinery.</p>
    <ul class="card-list"><li>HMI's</li><li>MOTION CONTROL</li><li>ROBOTICS</li><li>VISION</li><li>INDUSTRIAL NETWORKS</li><li>FIELDBUS</li><li>PLC's</li><li>SCADA</li></ul>
    <a class="btn" href="#">View More</a>
  </article>
  <article class="card green">
    <h3 class="card-head">PROGRAMMING LANGUAGES</h3>
    <div class="card-photo" role="img" aria-label="Walking robot in a dark caged corridor" style="background:linear-gradient(#3a3a30,#121210)"></div>
    <p class="card-text">Design and implement control programs on PLC's, SCADA, HMI's, Vision Systems, Robots and Motion Controls specific to each application...</p>
    <ul class="card-list"><li>Batch</li><li>Java</li><li>C++</li><li>Javascript</li><li>IEC 61131 - 3 (PLC)</li><li>TPL / TPP</li><li>VAL+</li><li>Visual Basic</li></ul>
    <a class="btn" href="#">View More</a>
  </article>
  <article class="card blue">
    <h3 class="card-head">INDUSTRIES</h3>
    <div class="card-photo" role="img" aria-label="Chrome robot endoskeleton" style="background:linear-gradient(#5a4a40,#1c1612)"></div>
    <p class="card-text">Develop controls and mechanical specifications for machines to be used when purchasing equipment. Collaborate with the systems...</p>
    <ul class="card-list"><li>Assembly</li><li>Distribution</li><li>Manufacturing</li><li>Material Handling</li><li>Automotive</li><li>Food and Beverage</li><li>Golf Course / Irrigation</li><li>Packaging</li></ul>
    <a class="btn" href="#">View More</a>
  </article>
</main>

<footer class="site-footer">
  <nav class="footer-nav">Home<span class="sep">/</span>About us<span class="sep">/</span>Services<span class="sep">/</span>Solutions<span class="sep">/</span>Technologies<span class="sep">/</span>Support<span class="sep">/</span>News<span class="sep">/</span>Contact us</nav>
  <p class="copyright">©2015velengsolutions. All rights reserved.</p>
  <div class="social" aria-label="Social links"><span></span><span></span><span></span><span></span><span></span></div>
</footer>
</body>
</html>
```